Website improvements and Adding Functionalities at https://mervo.site/tarnovex

1.Search functionality
2.Payment process functionality
3. Application configuration
4. Registration functionality activation
5. Chat functionality
6.Language switching functionality (Portuguese & French)
7.Bespoke interactive modules
8. Automated web scraping and data synchronisation mechanisms
9. News Page
10.Webinar facilities
11. Basic SEO optimisation
12. Speed and performance optimisation
13. Security configuration
14. Google Analytics integration
15. Cross-browser and mobile testing
16. Website deployment and launch support

Target Market(s)

My target markets are companies, investors, suppliers and professionals with an interest in the Mozambican oil and gas sector

Industry/Entity Type

Oil and Gas

Coding

Coded - Design and coding required

Number of Pages Required

1 page

Requirements
Must have
• Improve the existing page at https://mervo.site/tarnovex and add the following features to it: 1. Search functionality 2. Payment process functionality 3. Application configuration 4. Activation of registration functionality 5. Chat functionality 6. Language switching functionality (Portuguese & French) 7. Bespoke interactive modules 8. Automated web scraping and data synchronisation mechanisms 9. News Page

```html
<!DOCTYPE html>
<html lang="en">
<head>
<meta charset="utf-8">
<title>Tarnovex – Mozambique Oil &amp; Gas Intelligence</title>
<link href="https://fonts.googleapis.com/css2?family=Anton&family=Poppins:wght@400;500;600&display=swap" rel="stylesheet">
<style>
:root{
  --navy:#241c4d;
  --navy-deep:#1d1640;
  --orange:#e84e2c;
  --orange-soft:#f7c3b6;
  --ink:#1f1a3a;
  --text:#3d3a4d;
  --white:#ffffff;
  --line:#e6e3ee;
}
*{box-sizing:border-box;margin:0;padding:0}
html,body{width:1200px;height:3937px;overflow:hidden}
body{position:relative;background:var(--white);font-family:"Poppins",sans-serif;color:var(--text)}
.abs{position:absolute}
.head{font-family:"Anton",sans-serif;font-weight:400;text-transform:uppercase;letter-spacing:.3px;color:var(--ink);line-height:1.1}
.accent{color:var(--orange)}
.btn{position:absolute;display:flex;align-items:center;justify-content:center;border-radius:40px;font-family:"Anton",sans-serif;text-transform:uppercase;font-size:10px;letter-spacing:.4px}
.btn-solid{background:var(--orange);color:var(--white)}
.btn-outline{border:1.5px solid var(--white);color:var(--white)}
.btn-white{background:var(--white);color:var(--orange)}

/* hero */
.hero{left:0;top:0;width:1200px;height:731px;background:linear-gradient(180deg,#2d2a8a 0%,#3a3c96 35%,#2f3d74 60%,#1c2236 100%)}
.topbar{left:0;top:0;width:1200px;height:38px;background:var(--navy-deep)}
.live{left:130px;top:12px;font-family:"Anton",sans-serif;font-size:9px;color:var(--white);text-transform:uppercase}
.search{left:680px;top:10px;width:232px;height:19px;background:var(--navy);border:1px solid #3d3670;border-radius:3px;font-size:7px;line-height:10px;color:#cfcbe3;padding:4px 8px}
.search .go{position:absolute;right:-1px;top:-1px;width:20px;height:19px;background:var(--orange);border-radius:3px}
.lang{left:948px;top:12px;font-family:"Anton",sans-serif;font-size:9px;color:var(--white);text-transform:uppercase}
.lang-opt{top:11px;width:16px;height:14px;font-family:"Anton",sans-serif;font-size:7px;color:var(--white);display:flex;align-items:center;justify-content:center;border-radius:2px}
.nav a{position:absolute;top:76px;font-family:"Anton",sans-serif;font-size:9.5px;color:var(--white);text-transform:uppercase;text-decoration:none}
.brand-mark{left:580px;top:8px;width:40px;height:40px;border-radius:50%;background:var(--orange)}
.brand-name{left:530px;top:78px;width:140px;text-align:center;font-family:"Anton",sans-serif;font-size:12px;letter-spacing:3px;color:var(--white)}
.hero-title{left:200px;top:192px;width:800px;text-align:center;font-size:42px;color:var(--white);line-height:1}
.hero-text{left:310px;top:296px;width:580px;text-align:center;font-size:10.5px;line-height:19px;color:var(--white)}
.scroll{left:1036px;top:718px;width:27px;height:27px;border-radius:50%;background:var(--orange);display:flex;align-items:center;justify-content:center}

/* how it works */
.how-title{left:191px;top:926px;font-size:32px}
.how-text{left:191px;top:1020px;width:370px;font-size:10.5px;line-height:19px}
.how-back{left:627px;top:849px;width:384px;height:394px;background:var(--orange);border-radius:6px}
.how-photo{left:607px;top:821px;width:385px;height:402px;border-radius:6px;background:linear-gradient(160deg,#1d3c6e,#2c6aa0 45%,#0e1d36)}
.badge{left:853px;top:1136px;width:158px;height:107px;background:var(--orange);border-radius:0 0 6px 6px;color:var(--white);padding:18px 24px}
.badge b{display:block;font-family:"Anton",sans-serif;font-size:44px;line-height:1;font-weight:400}
.badge span{font-size:10px}

/* access */
.access{left:0;top:1341px;width:1200px;height:971px;background:var(--orange)}
.access-title{left:0;top:1420px;width:1200px;text-align:center;font-size:32px;color:var(--white)}
.card{position:absolute;background:var(--white);border-radius:10px;padding:6px}
.card .img{display:block;height:191px;border-radius:8px}
.card h3{margin:18px 0 0 18px;font-size:19px}
.card p{margin:12px 18px 0 18px;font-size:10px;line-height:19px}

/* what is */
.dash{left:165px;top:2405px;width:453px;height:318px;border:1.5px solid var(--line);border-radius:10px;padding:12px;background:var(--white);box-shadow:0 4px 14px rgba(30,20,70,.08)}
.dash-screen{display:flex;width:100%;height:100%;border-radius:4px;overflow:hidden;background:#f4f4f8}
.dash-side{width:62px;background:var(--navy)}
.dash-main{flex:1;padding:10px;display:grid;grid-template-columns:repeat(4,1fr);grid-template-rows:30px 100px 1fr;gap:8px}
.dash-main div{background:var(--white);border-radius:4px}
.what-title{left:667px;top:2456px;font-size:32px}
.what-text{left:667px;top:2518px;width:370px;font-size:10.5px;line-height:19px}
.what-text p+p{margin-top:19px}

/* unique */
.uniq-title{left:0;top:2828px;width:1200px;text-align:center;font-size:32px}
.ucard{position:absolute;top:2911px;width:257px;height:288px;background:var(--white);border-radius:10px;box-shadow:0 6px 24px rgba(30,20,70,.08)}
.ucard .ico{position:absolute;left:24px;top:60px;width:50px;height:50px;border-radius:50%;background:var(--orange)}
.ucard .num{position:absolute;right:24px;top:58px;font-family:"Anton",sans-serif;font-size:50px;color:var(--orange-soft);line-height:1}
.ucard h3{position:absolute;left:24px;top:152px;font-size:19px}
.ucard p{position:absolute;left:24px;top:208px;width:210px;font-size:10px;line-height:19px}

/* cta + footer */
.footer{left:0;top:3437px;width:1200px;height:500px;background:var(--navy-deep)}
.cta{left:131px;top:3295px;width:938px;height:272px;border-radius:14px;background:linear-gradient(90deg,#5a2418 0%,#a8411a 45%,#e08a2c 70%,#6b2a16 100%)}
.cta-title{left:200px;top:3366px;font-size:34px;color:var(--white)}
.cta-text{left:200px;top:3446px;width:380px;font-size:10.5px;line-height:19px;color:var(--white)}
.f-brand{left:138px;top:3718px;display:flex;align-items:center;gap:14px}
.f-brand i{width:44px;height:44px;border-radius:50%;background:var(--orange);display:block}
.f-brand span{font-family:"Anton",sans-serif;font-size:18px;letter-spacing:3px;color:var(--white)}
.f-col h4{font-family:"Anton",sans-serif;font-weight:400;font-size:11px;color:var(--white);text-transform:uppercase;margin-bottom:12px}
.f-col li{list-style:none;font-size:9.5px;color:var(--white);line-height:18.5px}
.contact li{display:flex;gap:6px;align-items:flex-start}
.contact svg{flex:none;margin-top:5px}
.social{display:flex;gap:10px;margin-top:8px}
.social span{width:17px;height:17px;border-radius:50%;border:1px solid #4a4378}
.rule{left:131px;top:3884px;width:938px;height:1px;background:#3a3268}
.copy{left:0;top:3900px;width:1200px;text-align:center;font-size:9px;color:var(--white)}
.chat{left:1117px;top:3858px;width:54px;height:54px;border-radius:50%;background:var(--orange);border:4px solid var(--white);display:flex;align-items:center;justify-content:center}
</style>
</head>
<body>

<!-- HERO -->
<section class="abs hero" role="img" aria-label="Night view of an illuminated oil refinery with towers and pipework under a blue sky"></section>
<div class="abs topbar"></div>
<div class="abs live">Live Mozambique market sync active</div>
<div class="abs search">Search tenders, suppliers, data...<span class="go"></span></div>
<div class="abs lang">Language:</div>
<div class="abs lang-opt" style="left:1004px;background:var(--orange)">EN</div>
<div class="abs lang-opt" style="left:1031px">PT</div>
<div class="abs lang-opt" style="left:1048px">FR</div>

<div class="abs brand-mark"></div>
<nav class="nav">
  <svg class="abs" style="left:148px;top:75px" width="12" height="11" viewBox="0 0 12 11"><path d="M6 0 12 5H10V11H7V7H5V11H2V5H0Z" fill="#e84e2c"/></svg>
  <a style="left:176px">Industry Insights</a>
  <a style="left:277px">Oil &amp; Gas Opportunities</a>
  <a style="left:401px">Supplier &amp; Company Network</a>
  <a style="left:677px">Industry News</a>
  <a style="left:765px">Legal Framework</a>
</nav>
<div class="abs brand-name">TARNOVEX CO</div>
<div class="btn btn-solid" style="left:859px;top:63px;width:89px;height:36px">Sign In</div>
<div class="btn btn-outline" style="left:954px;top:63px;width:115px;height:36px">Contact Us</div>

<h1 class="abs head hero-title">Access Mozambique’s Oil &amp; Gas<br>Industry <span class="accent">Intelligence</span> in One Platform</h1>
<p class="abs hero-text">Tarnovex is a modern online connection and consulting platform designed to facilitate access to the Mozambican Oil and Gas industry through premium industry insights, supplier information, tenders, legal frameworks, and strategic project data.</p>
<div class="btn btn-solid" style="left:540px;top:371px;width:120px;height:36px">Register Now</div>
<div class="abs scroll"><svg width="10" height="10" viewBox="0 0 10 10"><path d="M5 1V9M2 6 5 9 8 6" stroke="#fff" stroke-width="1.4" fill="none"/></svg></div>

<!-- HOW IT WORKS -->
<h2 class="abs head how-title">How the Platform<br><span class="accent">Works</span></h2>
<p class="abs how-text">The platform operates through a secure automated payment system that grants registered users access to premium and exclusive content. By subscribing, users receive organized industry intelligence designed to save time, improve market access, and support strategic business growth within Mozambique’s energy sector.</p>
<div class="btn btn-solid" style="left:191px;top:1137px;width:120px;height:36px">Learn More</div>
<div class="abs how-back"></div>
<div class="abs how-photo" role="img" aria-label="Laptop showing data charts in front of a lit industrial plant at dusk"></div>
<div class="abs badge"><b>25+</b><span>Year Experience</span></div>

<!-- WHAT YOU WILL ACCESS -->
<section class="abs access"></section>
<h2 class="abs head access-title">What You Will Access</h2>

<div class="card" style="left:199px;top:1489px;width:243px;height:334px">
  <div class="img" style="background:linear-gradient(150deg,#5d6a72,#c0622e 60%,#3a3f44)" role="img" aria-label="Engineer in hard hat working on a laptop at a refinery"></div>
  <h3 class="head">Hydrocarbon Industry<br>Information</h3>
  <p>General information and insights about Mozambique’s oil and gas sector.</p>
</div>
<div class="card" style="left:454px;top:1489px;width:245px;height:334px">
  <div class="img" style="background:linear-gradient(150deg,#6d7a7c,#2fb89a 55%,#2c3a3c)" role="img" aria-label="Green gas pipeline valves in a processing facility"></div>
  <h3 class="head">Main Gas<br>Projects</h3>
  <p>Details about major gas and energy projects operating in Mozambique.</p>
</div>
<div class="card" style="left:709px;top:1489px;width:247px;height:334px">
  <div class="img" style="background:linear-gradient(150deg,#8a96a4,#d5dbe2 55%,#4a5664)" role="img" aria-label="Two engineers reviewing data on a laptop in a plant"></div>
  <h3 class="head">Supplier &amp; Company<br>Database</h3>
  <p>Mozambican companies capable of meeting Level 3 supply requirements.</p>
</div>
<div class="card" style="left:199px;top:1833px;width:243px;height:334px">
  <div class="img" style="background:linear-gradient(150deg,#d9dcd8,#8f9590 55%,#3a3c3a)" role="img" aria-label="Business partners shaking hands over a desk"></div>
  <h3 class="head">Tender<br>Opportunities</h3>
  <p>Short, medium, and long-term tenders within the industry.</p>
</div>
<div class="card" style="left:454px;top:1833px;width:245px;height:334px">
  <div class="img" style="background:linear-gradient(150deg,#e8e6e2,#b59a86 55%,#6a5446)" role="img" aria-label="Two colleagues reviewing a document together"></div>
  <h3 class="head">Ownership &amp;<br>Access</h3>
  <p>Information related to hydrocarbon reserves and sector participation.</p>
</div>
<div class="card" style="left:709px;top:1833px;width:247px;height:334px">
  <div class="img" style="background:linear-gradient(150deg,#7d8792,#4b5058 55%,#c89a5a)" role="img" aria-label="Aerial view of a city business district at dusk"></div>
  <h3 class="head">Local Company<br>Capacity</h3>
  <p>Business integration opportunities within the oil and gas sector.</p>
</div>
<div class="btn btn-white" style="left:519px;top:2197px;width:162px;height:37px">View All What You Will Access</div>

<!-- WHAT IS -->
<div class="abs dash">
  <div class="dash-screen" role="img" aria-label="Platform dashboard overview with statistics, charts and project lists">
    <div class="dash-side"></div>
    <div class="dash-main">
      <div></div><div></div><div></div><div></div>
      <div style="grid-column:span 2"></div><div></div><div style="grid-row:span 2"></div>
      <div></div><div style="grid-column:span 2"></div>
    </div>
  </div>
</div>
<h2 class="abs head what-title">What is <span class="accent">Tarnovex?</span></h2>
<div class="abs what-text">
  <p>Tarnovex is a unique online platform built to connect businesses, investors, suppliers, and professionals with valuable information about the Mozambican Oil &amp; Gas sector.</p>
  <p>Through a secure digital paywall system, users gain access to organized, up-to-date, and carefully selected industry information that supports better decision-making, market understanding, and business opportunities within Mozambique’s growing hydrocarbons industry.</p>
</div>

<!-- UNIQUE -->
<h2 class="abs head uniq-title">Why Tarnovex is <span class="accent">Unique</span></h2>
<div class="ucard" style="left:199px"><span class="ico"></span><span class="num">01</span>
  <h3 class="head">Up-to-Date Industry<br>Intelligence</h3>
  <p>Receive frequent updates about developments in Mozambique’s Oil &amp; Gas sector.</p></div>
<div class="ucard" style="left:468px"><span class="ico"></span><span class="num">02</span>
  <h3 class="head">High-Quality<br>Curated Information</h3>
  <p>Access carefully selected and synthesized information tailored to industry stakeholders.</p></div>
<div class="ucard" style="left:738px;width:263px"><span class="ico"></span><span class="num">03</span>
  <h3 class="head">Time-Saving<br>Access</h3>
  <p>Avoid spending hours searching through scattered online sources with organized and accessible content in one platform.</p></div>

<!-- CTA + FOOTER -->
<footer class="abs footer"></footer>
<div class="abs cta" role="img" aria-label="Offshore oil platform silhouetted against an orange sunset sea"></div>
<h2 class="abs head cta-title">Start Exploring Mozambique’s<br>Oil &amp; Gas Opportunities</h2>
<p class="abs cta-text">Register today to access premium industry information, supplier networks, tenders, and strategic market insights through Tarnovex.</p>
<div class="btn btn-outline" style="left:200px;top:3495px;width:123px;height:36px">Register Now</div>
<div class="btn btn-white" style="left:336px;top:3495px;width:120px;height:36px">Contact Us</div>

<div class="abs f-brand"><i></i><span>TARNOVEX CO</span></div>
<div class="abs f-col" style="left:440px;top:3660px"><h4>Quick Links</h4><ul>
  <li>Home</li><li>Industry Insights</li><li>Oil &amp; Gas Opportunities</li><li>Supplier &amp; Company Network</li><li>Industry News</li><li>Legal Framework</li><li>Sign In</li><li>Contact us</li></ul></div>
<div class="abs f-col" style="left:634px;top:3660px"><h4>What You Will Access</h4><ul>
  <li>Hydrocarbon Industry Information</li><li>Main Gas Projects</li><li>Supplier &amp; Company Database</li><li>Industry Contacts</li><li>Tender Opportunities</li><li>Ownership &amp; Access</li><li>Legal Framework</li><li>Local Company Capacity</li><li>Tender Application Guidance</li></ul></div>
<div class="abs f-col contact" style="left:850px;top:3660px;width:230px"><h4>Contact Us</h4><ul>
  <li><svg width="8" height="8" viewBox="0 0 8 8"><rect x="0" y="1" width="8" height="6" rx="1" fill="#e84e2c"/></svg>contacto@tarnovex.site</li>
  <li><svg width="8" height="9" viewBox="0 0 8 9"><path d="M4 0C6 0 8 1.6 8 3.6 8 6 4 9 4 9S0 6 0 3.6C0 1.6 2 0 4 0Z" fill="#e84e2c"/></svg><span style="line-height:13px;padding-top:2px">12 Harbour Lane, Riverside District, Port Meridian</span></li>
  <li><svg width="8" height="8" viewBox="0 0 8 8"><circle cx="4" cy="4" r="4" fill="#e84e2c"/></svg>www.tarnovex.site</li></ul>
  <h4 style="margin-top:16px">Follow Us</h4>
  <div class="social"><span></span><span></span><span></span><span></span></div>
</div>
<div class="abs rule"></div>
<div class="abs copy">© 2026 by Tarnovex Co. All Rights Reserved.</div>
<div class="abs chat"><svg width="22" height="20" viewBox="0 0 22 20"><path d="M3 1H19A2 2 0 0 1 21 3V12A2 2 0 0 1 19 14H9L4 18V14H3A2 2 0 0 1 1 12V3A2 2 0 0 1 3 1Z" fill="#fff"/><circle cx="7" cy="7.5" r="1.3" fill="#e84e2c"/><circle cx="11" cy="7.5" r="1.3" fill="#e84e2c"/><circle cx="15" cy="7.5" r="1.3" fill="#e84e2c"/></svg></div>

</body>
</html>
```